Web Design Project

We are looking for a unified design of Corporate Website, Stationary (Including Letterhead and Envelopes), Business Cards, Email Footers and Sales & Marketing Brochures.

Color palette should include:
Black (R: 24, G:24, B:24)
Red (R:206, G:0, B:39)
Dark Grey (R:51, G:51, B:51)
Light Grey/Silver (R:203, G:203, B:203)

As we do business in North America and the UK, designs should be reflective of standard sizing for both regions.

Check out our website to better understand who we are: www.KLVR.com and a copy of our Logo has been uploaded for reference.
Updates

Hello all, we had not anticipated the volume of unique, high quality designs we have received, thank you all for your submissions. A team review of all designs will take place the week of December 8th, and final decisions and selections made. Thank you again

Target Market(s)

Automotive Parts Wholesalers, Vehicle Repair Specialists, Automotive Parts Manufacturers, Automotive Insurance

Industry/Entity Type

Business

Font styles to use
Sans Serif

Requirements
Must have
• - Color palette should include:
- Black (R: 24, G:24, B:24)
- Red (R:206, G:0, B:39)
- Dark Grey (R:51, G:51, B:51)
- Light Grey/Silver (R:203, G:203, B:203)
Should not have
• No Animations

```html
<!DOCTYPE html>
<html lang="en">
<head>
<meta charset="utf-8">
<title>Kelver Parts Solutions</title>
<link href="https://fonts.googleapis.com/css2?family=Open+Sans:ital,wght@0,400;0,600;0,700;1,400&family=Carlito:wght@400;700&display=swap" rel="stylesheet">
<style>
:root{
  --black:#181818;
  --red:#ce0027;
  --dark:#333333;
  --silver:#cbcbcb;
  --text:#777777;
  --white:#ffffff;
}
*{margin:0;padding:0;box-sizing:border-box}
html,body{width:799px;height:1200px;overflow:hidden;background:var(--white)}
body{position:relative;font-family:"Carlito","Open Sans",sans-serif;color:var(--text)}
.abs{position:absolute}

/* header */
.brand{left:88px;top:22px;display:flex;align-items:center;gap:8px}
.brand-mark{width:38px;height:38px;border-radius:50%;border:4px solid var(--silver)}
.brand-name{font-family:"Open Sans",sans-serif;font-weight:700;font-size:15px;line-height:17px;color:var(--black);letter-spacing:.5px;text-transform:uppercase}
.search{left:500px;top:26px;width:212px;height:27px;border:1px solid var(--silver);font-size:9px;color:#999;padding:8px 9px;font-family:"Open Sans",sans-serif}
.search svg{position:absolute;right:9px;top:6px}

/* nav */
.nav{left:0;top:83px;width:799px;height:50px;background:var(--black);border-bottom:2px solid var(--white)}
.nav ul{list-style:none;position:absolute;left:87px;top:0;display:flex;height:50px}
.nav li{font-family:"Open Sans",sans-serif;font-size:8.5px;color:var(--white);line-height:50px;padding:0 10px;text-transform:uppercase}
.nav li.active{background:var(--red);padding:0 17px;margin-right:0}
.nav li+li{margin-left:9px}

/* hero */
.hero{left:0;top:136px;width:799px;height:349px;background:linear-gradient(90deg,#3a3a3a 0%,#8a8a8a 35%,#bdbdbd 55%,#6e6e6e 75%,#a8a8a8 100%)}
.hero-title{left:87px;top:198px;font-family:"Open Sans",sans-serif;font-weight:700;font-size:35px;line-height:47px;color:var(--white);text-transform:uppercase}
.hero-text{left:87px;top:297px;width:310px;font-family:"Open Sans",sans-serif;font-size:11px;line-height:19px;color:var(--white)}
.btn{display:block;background:var(--red);color:var(--white);font-family:"Open Sans",sans-serif;font-weight:600;font-size:12px;text-align:center}
.hero .btn,.btn.hero-btn{left:87px;top:371px;width:106px;height:34px;line-height:34px;font-size:13px}
.dots{left:87px;top:455px;display:flex;gap:2px}
.dots i{width:7px;height:7px;border-radius:50%;background:var(--black);display:block}
.dots i:first-child{background:var(--red)}

/* sections */
.h2{font-family:"Open Sans",sans-serif;font-weight:600;font-size:16px;color:var(--black);text-transform:uppercase}
.h2 span{color:var(--red)}
.para{font-size:10px;line-height:16px;color:var(--text)}
.btn.sm{width:90px;height:32px;line-height:32px}

.video{left:498px;top:518px;width:214px;height:174px;background:var(--black);padding:4px}
.video-screen{width:206px;height:152px;background:linear-gradient(180deg,#111 0%,#2a1a12 55%,#8a8a8a 80%,#333 100%);position:relative}
.video-name{position:absolute;left:18px;top:26px;font-family:"Open Sans",sans-serif;font-weight:700;font-size:14px;color:var(--white);text-transform:uppercase;display:flex;align-items:center;gap:6px}
.video-name i{width:24px;height:24px;border-radius:50%;border:3px solid var(--white);display:block}
.play{position:absolute;left:88px;top:70px;width:30px;height:20px;background:var(--white);border-radius:5px}
.play:after{content:"";position:absolute;left:12px;top:5px;border-left:8px solid var(--black);border-top:5px solid transparent;border-bottom:5px solid transparent}
.video-bar{height:14px;position:relative}
.video-bar b{position:absolute;left:2px;top:2px;width:110px;height:2px;background:var(--red)}
.video-bar s{position:absolute;left:112px;top:2px;width:92px;height:2px;background:#555}

.service{top:804px;width:190px}
.service-icon{position:absolute;left:0;top:0;width:32px;height:32px;background:var(--dark);border-radius:3px}
.service h3{position:absolute;left:58px;top:0;font-family:"Carlito",sans-serif;font-weight:700;font-size:12.5px;line-height:16px;color:var(--red)}
.service .para{position:absolute;left:0;top:46px;width:180px}
.service .btn{position:absolute;left:0;top:106px}
.divider{top:804px;width:1px;height:140px;background:#e6e6e6}

.avatar{left:87px;top:1008px;width:70px;height:70px;border-radius:50%;border:1px solid var(--silver);background:radial-gradient(circle at 50% 40%,#e9d3b8 0%,#c9a36a 55%,#eeeeee 100%)}
.quote{left:168px;top:1008px;width:540px;font-style:italic;font-family:"Open Sans",sans-serif;font-size:9.5px;line-height:16px;color:#888}
.client{left:175px;top:1062px;font-style:italic;font-family:"Open Sans",sans-serif;font-size:9.5px;color:var(--red)}
.arrow{top:1026px}

/* footer */
.footer{left:0;top:1124px;width:799px;height:76px;background:var(--black)}
.footer ul{list-style:none;position:absolute;left:87px;top:18px;display:flex;gap:13px}
.footer li{font-family:"Open Sans",sans-serif;font-size:8.5px;color:#bbb}
.copy{position:absolute;left:87px;top:47px;font-family:"Open Sans",sans-serif;font-size:8.5px;color:#bbb}
.social{position:absolute;left:579px;top:16px;display:flex;gap:5px}
.social i{width:22px;height:22px;border-radius:50%;background:var(--white);display:block}
</style>
</head>
<body>

<header>
  <div class="abs brand"><i class="brand-mark"></i><div class="brand-name">Kelver<br>Parts Solutions</div></div>
  <div class="abs search">Search here
    <svg width="13" height="13" viewBox="0 0 13 13"><circle cx="5.5" cy="5.5" r="4.2" fill="none" stroke="#aaa" stroke-width="1.5"/><line x1="8.6" y1="8.6" x2="12" y2="12" stroke="#aaa" stroke-width="1.8"/></svg>
  </div>
</header>

<nav class="abs nav">
  <ul>
    <li class="active">Home</li>
    <li>Intelligent Sales &amp; Marketing</li>
    <li>Kelver Awards</li>
    <li>References</li>
    <li>About Us</li>
    <li>Careers</li>
    <li>Contact Us</li>
  </ul>
</nav>

<section class="abs hero" role="img" aria-label="Smiling mechanic in overalls holding a wrench beside an open car bonnet, black and white photo"></section>
<h1 class="abs hero-title">Kelver Parts<br>Solutions</h1>
<p class="abs hero-text">Since 1988 we have provided wholesale parts sales and marketing solutions to automotive parts, services and repairer networks throughout Canada, USA and UK.</p>
<a class="abs btn hero-btn">Read More</a>
<div class="abs dots"><i></i><i></i><i></i><i></i></div>

<section>
  <h2 class="abs h2" style="left:87px;top:511px">Welcome to <span>Kelver Parts Solutions</span></h2>
  <p class="abs para" style="left:87px;top:541px;width:395px">Lorem ipsum dolor sit amet, no his commune vivendum abhorreant, hinc assueverit quo te. Ad has aperiri repudiare. Vis aeterno numquam ne, zril neglegentur ad pri, est te nullam corpora. Et sit diceret sententiae. Vix prima cetero ex, mei purto corpora apeirian ea.</p>
  <p class="abs para" style="left:87px;top:595px;width:395px">Lorem ipsum dolor sit amet, no his commune vivendum abhorreant, hinc assueverit quo te. Ad has aperiri repudiare. Vis aeterno numquam ne, zril neglegentur ad pri, est te nullam corpora. Et sit diceret sententiae. Vix prima cetero ex, mei purto corpora apeirian ea.</p>
  <a class="abs btn sm" style="left:87px;top:658px">Read More</a>
  <div class="abs video">
    <div class="video-screen" role="img" aria-label="Company video thumbnail with car parts close-up">
      <div class="video-name"><i></i>Kelver</div>
      <div class="play"></div>
    </div>
    <div class="video-bar"><b></b><s></s></div>
  </div>
</section>

<section>
  <h2 class="abs h2" style="left:87px;top:718px">What <span>we do</span></h2>
  <p class="abs para" style="left:87px;top:750px;width:625px">Quo ea decore saperet, ea graeci splendide vim, eius magna possit est ei. Nulla facilisis qualisque usu id, ius assentior signiferumque te, ex cum eius graecis. Ad dicat detracto mea. Vel ei alii officiis sententiae, ex has lorem simul. Inani alterum minimum eos cu.</p>

  <div class="abs service" style="left:87px">
    <i class="service-icon" role="img" aria-label="Delivery car with dollar sign icon"></i>
    <h3>Automotive Parts<br>Wholesalers</h3>
    <p class="para">Unum impedit democritum ex nec. Dicit meliore mel ut. Etiam nostro vix in. Menandri conclusionemque cu mei.</p>
    <a class="btn sm">Read More</a>
  </div>
  <i class="abs divider" style="left:282px"></i>
  <div class="abs service" style="left:313px">
    <i class="service-icon" role="img" aria-label="Gear and wrench icon"></i>
    <h3 style="left:47px">Vehicle Repair<br>Specialists</h3>
    <p class="para">Unum impedit democritum ex nec. Dicit meliore mel ut. Etiam nostro vix in. Menandri conclusionemque cu mei.</p>
    <a class="btn sm">Read More</a>
  </div>
  <i class="abs divider" style="left:510px"></i>
  <div class="abs service" style="left:540px">
    <i class="service-icon" role="img" aria-label="Puzzle pieces icon"></i>
    <h3 style="left:42px">Automotive Parts<br>Manufacturers</h3>
    <p class="para">Unum impedit democritum ex nec. Dicit meliore mel ut. Etiam nostro vix in. Menandri conclusionemque cu mei.</p>
    <a class="btn sm">Read More</a>
  </div>
</section>

<section>
  <h2 class="abs h2" style="left:87px;top:971px">Our <span>client says</span></h2>
  <svg class="abs arrow" style="left:40px" width="14" height="30" viewBox="0 0 14 30"><polyline points="13,1 1,15 13,29" fill="none" stroke="#d5d5d5" stroke-width="1.5"/></svg>
  <svg class="abs arrow" style="left:742px" width="14" height="30" viewBox="0 0 14 30"><polyline points="1,1 13,15 1,29" fill="none" stroke="#d5d5d5" stroke-width="1.5"/></svg>
  <div class="abs avatar" role="img" aria-label="Portrait photo of a smiling client"></div>
  <p class="abs quote">“ Ullum option sensibus et est, mei affert vocibus interpretaris cu. At eos utinam tamquam. Tibique moderatius definitionem vis te, nullam cotidieque cum an. Quo eirmod sadipscing at. Ullum option sensibus et est, mei affert vocibus interpretaris cu. At eos utinam tamquam. Tibique moderatius definitionem vis te, nullam cotidieque. ”</p>
  <p class="abs client">Client Name</p>
</section>

<footer class="abs footer">
  <ul>
    <li>Home</li><li>Intelligent sales &amp; Marketing</li><li>Kelver Awards</li><li>References</li><li>About Us</li><li>Careers</li><li>Contact Us</li>
  </ul>
  <p class="copy">Copyright @ 2014 Kelver Parts Solutions.All Rights Reserved.</p>
  <div class="social" aria-label="Social links"><i></i><i></i><i></i><i></i><i></i></div>
</footer>

</body>
</html>
```